Stationery Design needed for logo design project

This project is linked to Pediatric Therapy Clinic for children with autism and other special needs needs new logo design.

Our company needs a Stationery Design. Please refer to our original project in the link above.

Reason: Too much to do right now while enjoying Christmas with all my family!

```html
<!DOCTYPE html>
<html lang="en">
<head>
<meta charset="utf-8">
<title>Bright Steps Stationery</title>
<link href="https://fonts.googleapis.com/css2?family=Open+Sans:wght@400;600;700;800&display=swap" rel="stylesheet">
<style>
  :root{
    --bg:#eceef1;
    --paper:#ffffff;
    --ink:#3a3a3a;
    --muted:#6b6b6b;
    --accent-red:#e8452c;
    --flap-teal:#3cbfca;
    --sign:#4a4a4a;
  }
  *{margin:0;padding:0;box-sizing:border-box}
  html,body{width:1200px;height:937px;overflow:hidden;background:var(--bg);
    font-family:"Open Sans",Arial,sans-serif;color:var(--ink)}
  .canvas{position:relative;width:1200px;height:937px}
  .sheet{position:absolute;background:var(--paper)}

  /* brand name */
  .brand-name{display:block;font-weight:700;color:var(--ink);line-height:1.1;white-space:nowrap}

  /* letterhead */
  .letterhead{left:184px;top:66px;width:389px;height:546px}
  .letterhead .brand-name{position:absolute;left:22px;top:48px;font-size:20px}
  .contact{position:absolute;text-align:right;font-size:5.6px;line-height:1.5;color:var(--muted);font-style:normal}
  .letterhead .contact{right:18px;top:24px}
  .letter{position:absolute;left:38px;top:140px;width:300px;font-size:5.3px;line-height:1.55;color:var(--ink)}
  .letter p{margin-bottom:9px}
  .letter .sender{font-weight:700}
  .signature{width:26px;height:16px;background:var(--sign);opacity:.25;border-radius:3px;margin-bottom:6px}

  /* folder */
  .folder{left:636px;top:40px;width:460px;height:577px}
  .folder .brand-name{position:absolute;left:0;right:0;top:300px;text-align:center;font-size:40px}

  /* business cards */
  .card{width:177px;height:100px}
  .card-back{left:45px;top:658px}
  .card-back .contact{right:9px;top:38px;font-size:5.4px}
  .card-back .web{position:absolute;left:6px;bottom:6px;font-size:5.4px;color:var(--muted)}
  .card-back .web b{color:var(--accent-red);font-weight:600}
  .card-front{left:45px;top:784px}
  .card-front .brand-name{position:absolute;left:12px;top:44px;font-size:12px}
  .card-front .holder{position:absolute;right:10px;bottom:14px;text-align:right;font-size:6.8px;line-height:1.25}
  .card-front .holder .person{color:var(--accent-red);font-weight:600}
  .card-front .holder .role{color:var(--muted)}

  /* envelopes */
  .envelope{width:432px;height:207px}
  .envelope-front{left:265px;top:673px}
  .envelope-front .brand-block{position:absolute;left:22px;top:56px}
  .envelope-front .brand-name{font-size:17px}
  .envelope-front .return{display:block;font-size:4.6px;font-weight:700;color:var(--ink);margin-top:4px}
  .envelope-back{left:737px;top:673px}
  .flap{position:absolute;left:0;top:0;width:100%;height:72px;background:var(--flap-teal);
    border-radius:0 0 40px 40px;display:flex;align-items:center;justify-content:center}
  .flap .web{color:#fff;font-size:11px;letter-spacing:.28em;font-weight:400}
</style>
</head>
<body>
<main class="canvas">

  <section class="sheet letterhead">
    <span class="brand-name">Bright Steps</span>
    <address class="contact">
      2400 Maple Grove Ln<br>Austin TX 78701<br>512.555.0142<br>hello@brightsteps.com
    </address>
    <article class="letter">
      <p>July 2, 2012</p>
      <p><span class="sender">Dear Cli,</span><br>ABC Building, def St., Country Name</p>
      <p>Thank you for choosing our clinic for your child's care. We are glad to welcome your family and look forward to working together. Our therapists will contact you soon to schedule a first visit and talk through your goals for the coming months.</p>
      <p>Please bring any recent reports and a list of questions you would like to discuss with our team.</p>
      <p style="margin-top:16px">Each plan is built around play, routine and the strengths your child already shows. Parents are part of every step, and we share simple activities to practise at home between sessions so progress carries into daily life.</p>
      <p>Best Regards,</p>
      <div class="signature" role="img" aria-label="Handwritten signature of the director"></div>
      <p><span class="sender">Martin Cole</span><br>Director<br><br>ABC Building, def St., Country Name</p>
    </article>
  </section>

  <section class="sheet folder">
    <span class="brand-name">Bright Steps</span>
  </section>

  <section class="sheet card card-back">
    <address class="contact">
      2400 Maple Grove Ln<br>Austin TX 78701<br>512.555.0142<br>hello@brightsteps.com
    </address>
    <span class="web">www.<b>brightsteps</b>.com</span>
  </section>

  <section class="sheet card card-front">
    <span class="brand-name">Bright Steps</span>
    <div class="holder">
      <div class="person">Dana Whitfield</div>
      <div class="role">Owner</div>
    </div>
  </section>

  <section class="sheet envelope envelope-front">
    <div class="brand-block">
      <span class="brand-name">Bright Steps</span>
      <span class="return">2400 Maple Grove Ln, Austin TX 78701</span>
    </div>
  </section>

  <section class="sheet envelope envelope-back">
    <div class="flap"><span class="web">www.brightsteps.com</span></div>
  </section>

</main>
</body>
</html>
```